Gobal construction supply company needs new business card design

I need a business card design for my global supply company using an existing logo. i will be looking to print these on rounded corner cards with the black background version of my logo on the back. on the front white background, my logo again and my simple details.

```html
<!DOCTYPE html>
<html lang="en">
<head>
<meta charset="utf-8">
<title>Southern Crest Supply – Business Card</title>
<link href="https://fonts.googleapis.com/css2?family=Roboto:wght@400;500;700&display=swap" rel="stylesheet">
<style>
  :root {
    --page-bg: #c9c9c9;
    --card-dark: #1b1b1b;
    --card-light: #f2f2f2;
    --ink-light: #ffffff;
    --ink-dark: #111111;
    --accent-red: #d40000;
  }
  * { margin: 0; padding: 0; box-sizing: border-box; }
  html, body { width: 1200px; height: 960px; overflow: hidden; }
  body {
    background: var(--page-bg);
    font-family: "Roboto", Arial, sans-serif;
    position: relative;
  }
  .card {
    position: absolute;
    left: 300px;
    width: 600px;
    height: 343px;
    border-radius: 22px;
    overflow: hidden;
  }
  .card--back { top: 123px; background: var(--card-dark); }
  .card--front { top: 495px; background: var(--card-light); }
  .front-band {
    position: absolute;
    inset: 0;
    width: 600px;
    height: 343px;
  }
  .brand {
    position: absolute;
    display: flex;
    align-items: center;
    gap: 10px;
    font-weight: 700;
    letter-spacing: 0.5px;
    text-transform: uppercase;
    white-space: nowrap;
  }
  .brand__dot {
    width: 20px; height: 20px;
    border-radius: 50%;
    background: var(--accent-red);
    flex: none;
  }
  .card--back .brand {
    left: 50%; top: 158px;
    transform: translateX(-50%);
    font-size: 26px;
    color: var(--ink-light);
  }
  .card--front .brand {
    left: 425px; top: 258px;
    transform: translateX(-50%);
    font-size: 22px;
    color: var(--ink-dark);
  }
  .contact {
    position: absolute;
    left: 41px; top: 40px;
    color: var(--ink-light);
  }
  .contact__name { font-size: 22px; font-weight: 700; line-height: 26px; }
  .contact__role { font-size: 14px; font-weight: 700; color: var(--accent-red); line-height: 16px; }
  .contact__lines { margin-top: 20px; font-size: 14px; line-height: 19px; }
</style>
</head>
<body>
  <section class="card card--back" aria-label="Card back">
    <div class="brand"><span>Southern Crest Supply</span><span class="brand__dot"></span></div>
  </section>

  <section class="card card--front" aria-label="Card front">
    <svg class="front-band" viewBox="0 0 600 343" aria-hidden="true">
      <polygon points="0,0 402,0 176,343 0,343" fill="var(--card-dark)"/>
    </svg>
    <div class="contact">
      <p class="contact__name">DANIEL HART</p>
      <p class="contact__role">CEO/FOUNDER</p>
      <div class="contact__lines">
        <p>555 210 4836</p>
        <p>daniel@southerncrestsupply.com</p>
        <p>www.southerncrestsupply.com</p>
      </div>
    </div>
    <div class="brand"><span>Southern Crest Supply</span><span class="brand__dot"></span></div>
  </section>
</body>
</html>
```